Contemporary Business card for Event Manager

Needed for my startup events company in Melbourne. Events I manage will be based within the fashion industry, sporting events, product launches etc. Not weddings or small dinner parties. Therfore I am after something professional and aimed at high end corporate market; but with the added emphasis on not being too conservative or boring. I am happy with a pop of colour e.g. yellow or copper foil.

Target Market(s)

fashion industry, design industry, high end sporting events e.g. Polo, Grand Prix, corporate clients,

Industry/Entity Type

Fashion

Contact Information for Business Card

side 1
Lucy Brandt (can be upper or lower case, have a feature full stop between first and surname, or at the end of the nameetc) I am open to ideas. I would also be fine with my initials or name as a logo on the front (if this is the case my full name would need to go on the second side of the card.
2nd side:
Mobile: +61 400 817 263
email: lucy.brandt@mailnest.com.au

on one side of the card:
event management | brand activation | Advisory Services

Font styles to use
Serif
Sans Serif

Requirements
Must have
• side 2 must have
• mobile number
• email address
• event management | brand activation | Advisory Services
• ** my full name (Lucy Brandt) must be on the card somewhere)
Nice to have
• 1st side
• I see the card stock being either a dark grey, light grey, natural white or black (all matt colours on unprocessed card). I see the writing being copper foil, or foil white or foil black.
• To give you a feel for me, think: contemporary, minimalist, I love line drawings, concrete, white with grey vein marble, copper, white, grey, black...yes I do like colour....yellow (but pops of colour) ;) I would like the card to look designer but 'on trend' as I deal with a lot of design and fashion clients....styles - think the sophistication and simplicity of Vireaux or urban contemporary.
• some examples of what I like. Although please don't leet this limit you...I really am happy to have something a little more urban or design focused like a line drawing of an object, person too or a photo image too.
• https://www.moodtackle.com/pin/830165427719302846/
• https://www.moodtackle.com/pin/607281935540173268/
• https://www.moodtackle.com/pin/318746205913457092/
• https://www.moodtackle.com/pin/41983627530918476/
• https://www.moodtackle.com/pin/53128940672419087/
• https://www.moodtackle.com/pin/90316284750638152/
• https://www.moodtackle.com/pin/734092618450362918/
• https://www.moodtackle.com/pin/926354081736215407/
• https://www.moodtackle.com/pin/481627093518704356/
Should not have
• should not look commercial or have cartoonish looking logos. However happy with a simple line drawing or logo with initials etc.

```html
<!DOCTYPE html>
<html lang="en">
<head>
<meta charset="utf-8">
<title>Lucy Brandt — Business Card</title>
<link href="https://fonts.googleapis.com/css2?family=Libre+Baskerville:wght@700&family=Tinos:wght@400&display=swap" rel="stylesheet">
<style>
  :root {
    --bg: #d9d4cb;
    --yellow: #f2e70f;
    --black: #0b0b0b;
    --ink: #1c1c1c;
    --card-w: 520px;
    --card-h: 318px;
  }
  * { margin: 0; padding: 0; box-sizing: border-box; }
  html, body { width: 1200px; height: 892px; overflow: hidden; }
  body {
    background: var(--bg);
    display: flex;
    align-items: center;
    justify-content: center;
    gap: 56px;
  }
  .card {
    width: var(--card-w);
    height: var(--card-h);
    position: relative;
    box-shadow: 0 10px 28px rgba(0,0,0,.25);
    overflow: hidden;
  }
  .card-front {
    background: var(--yellow);
    display: flex;
    align-items: center;
    justify-content: center;
  }
  .name {
    font-family: "Libre Baskerville", serif;
    font-weight: 700;
    font-size: 50px;
    color: var(--ink);
    letter-spacing: 0.5px;
  }
  .card-back {
    background: var(--black);
    font-family: "Tinos", serif;
    color: var(--yellow);
  }
  .phone {
    position: absolute;
    right: 46px;
    top: 78px;
    font-size: 34px;
    letter-spacing: 1px;
  }
  .services {
    position: absolute;
    right: 46px;
    top: 142px;
    text-align: right;
    font-size: 17px;
    line-height: 1.35;
  }
  .email-band {
    position: absolute;
    left: 0; right: 0;
    bottom: 30px;
    height: 40px;
    background: var(--yellow);
    display: flex;
    align-items: center;
    justify-content: flex-end;
    padding-right: 46px;
  }
  .email {
    font-size: 17px;
    color: var(--black);
  }
  .edge-stripe {
    position: absolute;
    left: 0; right: 0;
    bottom: 0;
    height: 14px;
    background: var(--yellow);
  }
</style>
</head>
<body>
  <section class="card card-front" aria-label="Card front">
    <h1 class="name">Lucy Brandt</h1>
  </section>

  <section class="card card-back" aria-label="Card back">
    <p class="phone">+61 400 817 263</p>
    <p class="services">Advisory Services<br>event management / brand activation</p>
    <div class="email-band"><p class="email">lucy.brandt@mailnest.com.au</p></div>
    <div class="edge-stripe"></div>
  </section>
</body>
</html>
```